Trendy E Juice Product Labels Required

We are looking for design for an e Juice label line (the liquids used in electronic cigarettes). What we need is 5 product labels which eventually will be printed on 95mm x 40mm labels. Obviously the image will be created much larger than this but the aspect ratio should be scalable down to this size.

What each label must have is I would need is a background, a monster character, and space for a product name incorporated in to the design. The brand on this line is "Velvet Orbit". Whilst creatively, we are completely open to any concept, there is certain text which is necessary for incorporation in to each label. The attached file, "Example Label" shows these elements. NOTE: the attached file IS NOT a finished label.
Updates

Reason: Not received a design that we wish to proceed with.

Target Market(s)

25-35 year old vapers

Industry/Entity Type

Electronic

Requirements
Should not have
• Anything that may be construed as being targeted toward children.

```html
<!DOCTYPE html>
<html lang="en">
<head>
<meta charset="utf-8">
<title>Velvet Orbit – E-Liquid Label</title>
<link rel="stylesheet" href="https://fonts.googleapis.com/css2?family=Barlow:wght@400;600&family=Barlow+Condensed:wght@400&family=Passion+One:wght@700&display=swap">
<style>
  :root {
    --brand-purple: #7d3f98;
    --brand-navy: #2b2a63;
    --mist-grey: #d9d8de;
    --mist-lilac: #e4d8ec;
    --paper: #ffffff;
    --ink: #111111;
  }
  * { box-sizing: border-box; margin: 0; padding: 0; }
  html, body { width: 1200px; height: 505px; overflow: hidden; background: var(--paper); }
  .label {
    position: relative; width: 1200px; height: 505px; overflow: hidden;
    background: var(--paper); color: var(--ink);
    font-family: "Barlow", Arial, sans-serif;
  }
  .band { position: absolute; left: 0; width: 100%; height: 37px; background: var(--brand-purple); }
  .band--top { top: 0; }
  .band--bottom { bottom: 0; }

  .legal { position: absolute; left: 56px; width: 250px; }
  .legal h2 { font-family: "Barlow", Arial, sans-serif; font-weight: 600; font-size: 25px; line-height: 1; letter-spacing: 0.5px; margin-bottom: 4px; }
  .legal p { font-size: 15.5px; line-height: 21.3px; }
  .legal--warning { top: 57px; }
  .legal--ingredients { top: 337px; width: 260px; }

  .brand-mist { position: absolute; left: 390px; top: 92px; width: 390px; height: 200px; }
  .brand-name {
    position: absolute; left: 400px; top: 108px; width: 370px; text-align: center;
    font-family: "Passion One", Impact, sans-serif; font-weight: 700;
    font-size: 88px; line-height: 76px; color: var(--brand-purple); letter-spacing: 1px;
  }

  .product-blob { position: absolute; left: 400px; top: 318px; width: 332px; height: 96px; }
  .product-name {
    position: absolute; left: 400px; top: 336px; width: 332px; text-align: center;
    font-family: "Barlow Condensed", "Arial Narrow", sans-serif; font-size: 33px; color: var(--paper);
  }
  .volume { position: absolute; left: 400px; top: 408px; width: 332px; text-align: center; font-size: 19px; }

  .contact { position: absolute; left: 845px; top: 58px; }
  .contact__lead { font-style: italic; font-size: 16px; }
  .social { display: flex; gap: 33px; margin-top: 13px; }
  .social__dot { width: 64px; height: 64px; border-radius: 50%; background: var(--brand-purple); }
  .contact__web { margin-top: 11px; font-weight: 600; font-size: 16px; line-height: 25px; }

  .distributor { position: absolute; left: 845px; top: 270px; font-size: 16.5px; line-height: 21.5px; }

  .safety-icons { position: absolute; left: 845px; top: 383px; width: 305px; height: 62px; }
</style>
</head>
<body>
<main class="label">
  <div class="band band--top"></div>

  <section class="legal legal--warning">
    <h2>WARNING</h2>
    <p>This product contains nicotine, a substance which is knows to cause birth defects. Do not swallow. Avoid contact with skin. Keep out of reach of children and pets. This product is intended for use by persons 18 and older. Pregnant women and those breast feeding should not use this product. May contain traces of nuts.</p>
  </section>

  <section class="legal legal--ingredients">
    <h2>INGREDIENTS</h2>
    <p>USP/EP Propelyn Glycol (XX%), USP/EP Vetetable Glycerin (XX%), USP/EP Nicotine, Natural and Artificial Flavorings.</p>
  </section>

  <svg class="brand-mist" viewBox="0 0 390 200" role="img" aria-label="Soft vapour clouds with the brand's monster character">
    <defs>
      <radialGradient id="mist" cx="50%" cy="55%" r="55%">
        <stop offset="0%" stop-color="#e7e3ec"/>
        <stop offset="100%" stop-color="#ffffff" stop-opacity="0"/>
      </radialGradient>
    </defs>
    <ellipse cx="195" cy="105" rx="190" ry="95" fill="url(#mist)"/>
  </svg>
  <h1 class="brand-name">VELVET<br>ORBIT</h1>

  <svg class="product-blob" viewBox="0 0 332 96" aria-hidden="true">
    <path d="M18 22 C60 -4 140 14 200 8 C262 2 318 6 328 40 C338 74 300 96 240 84 C190 74 140 94 90 88 C40 82 -4 70 2 46 C4 34 10 28 18 22 Z" fill="var(--brand-purple)"/>
  </svg>
  <div class="product-name">Product Name</div>
  <div class="volume">30ml</div>

  <section class="contact">
    <p class="contact__lead">Find us at:</p>
    <div class="social">
      <span class="social__dot"></span>
      <span class="social__dot"></span>
      <span class="social__dot"></span>
    </div>
    <p class="contact__web">www.velvetorbit.com<br>@velvetorbit</p>
  </section>

  <section class="distributor">
    <p>Distributed by:<br>Velvet Orbit<br>Address<br>Telephone</p>
  </section>

  <svg class="safety-icons" viewBox="0 0 305 62" aria-label="Recycle, caution, dispose responsibly and adults only icons" role="img">
    <g fill="none" stroke="var(--brand-purple)" stroke-width="7" stroke-linecap="round">
      <path d="M12 40 L30 8 L48 40 Z" stroke-linejoin="round"/>
    </g>
    <g fill="var(--brand-purple)">
      <path d="M30 2 L22 14 L38 14 Z"/>
      <path d="M52 44 L40 38 L44 54 Z"/>
      <path d="M8 44 L4 56 L20 50 Z"/>
      <path d="M112 4 L143 58 L81 58 Z"/>
    </g>
    <rect x="109" y="22" width="6" height="20" rx="2" fill="var(--paper)"/>
    <circle cx="112" cy="50" r="3.5" fill="var(--paper)"/>
    <g fill="var(--brand-purple)">
      <rect x="172" y="16" width="40" height="6" rx="2"/>
      <path d="M175 25 H209 L205 60 H179 Z"/>
    </g>
    <g stroke="var(--paper)" stroke-width="2.5">
      <line x1="186" y1="30" x2="187" y2="55"/><line x1="198" y1="30" x2="197" y2="55"/>
    </g>
    <circle cx="270" cy="31" r="26" fill="none" stroke="var(--brand-purple)" stroke-width="6"/>
    <text x="270" y="42" text-anchor="middle" font-family="Barlow, Arial, sans-serif" font-weight="600" font-size="30" fill="var(--brand-purple)">18</text>
    <line x1="252" y1="13" x2="288" y2="49" stroke="var(--brand-purple)" stroke-width="6"/>
  </svg>

  <div class="band band--bottom"></div>
</main>
</body>
</html>
```